International business needs business cards

Our company, DRV Ventures Inc. is in the business of supplying a range construction products with particular emphasis on CEMENT. We have developed our own brand - TORVAN SUPPLIES - with which to infiltrate the market. We are launching our brand of cement (TORVAN Type IS Cement) into the Caribbean which is unlike anything this market has ever seen. A monopoly has existed here for the past 60-odd years and the market has now opened to allow the importation of other brands and consumers are anxious and ready for change/improvement. We are very excited to be launching and want to make a great first impression. We will be conducting workshops and seminars (from government level to the hardware store owners) and we want our business card to give us the strong, confident introduction that we need.

Target Market(s)

construction; builders; engineers; home owners

Industry/Entity Type

Construction

Contact Information for Business Card

Marisol Depree
CEO
cell # 1 555 4180736
Ground floor,Lindell Plaza Suite 2734
George Town,Grand Cayman
Cayman Islands,KY1-4823
EMAIL: m.depree@drvventuresinc.example
web site drvventuresinc.example

COMPANY: skype info drv.ventures.example

second card
Yvette Brannock-Depree
CFO
CELL# 1 555 607 3941
George Town,Grand Cayman
Cayman Islands,KY1-4823
EMAIL: y.brannockdepree@drvventuresinc.example
website drvventuresinc.example

Requirements
Must have
• Business cards must display BOTH logos - DRV is the company and TORVAN is the brand.

```html
<!DOCTYPE html>
<html lang="en">
<head>
<meta charset="utf-8">
<title>DRV Ventures Inc. – Business Card</title>
<link href="https://fonts.googleapis.com/css2?family=Open+Sans:wght@400;600;700&display=swap" rel="stylesheet">
<style>
  :root {
    --page-bg: #ece8e3;
    --brand-red: #7b1519;
    --accent-red: #8e1b20;
    --card-white: #ffffff;
    --ink: #2e2e2e;
    --ink-dark: #111111;
    --badge-bg: #f4f4f4;
    --card-shadow: 0 14px 30px rgba(0,0,0,0.18);
  }
  * { box-sizing: border-box; margin: 0; padding: 0; }
  html, body {
    width: 1200px; height: 900px; overflow: hidden;
    background: var(--page-bg);
    font-family: "Open Sans", Arial, sans-serif;
  }
  .canvas { position: relative; width: 1200px; height: 900px; }

  .card {
    position: absolute;
    width: 560px; height: 320px;
    box-shadow: var(--card-shadow);
  }

  /* Front face */
  .card--front {
    left: 110px; top: 120px;
    background: var(--brand-red);
    display: flex; flex-direction: column; align-items: center; justify-content: center;
    gap: 22px;
  }
  .front-wordmark {
    color: var(--card-white);
    font-weight: 700;
    font-size: 40px;
    letter-spacing: 0.5px;
  }
  .brand-badge {
    width: 96px; height: 78px;
    background: var(--badge-bg);
  }

  /* Back face */
  .card--back {
    left: 530px; top: 460px;
    background: var(--card-white);
    color: var(--ink);
  }
  .contact {
    position: absolute; left: 290px; top: 34px;
    font-size: 14px; line-height: 1.45;
  }
  .contact__name { color: var(--accent-red); font-weight: 700; font-size: 19px; line-height: 1.2; }
  .contact__role { font-size: 14px; margin-bottom: 14px; }
  .contact__address { margin-bottom: 14px; }
  .contact__list { list-style: none; }
  .contact__item { display: flex; align-items: center; gap: 10px; }
  .contact__icon { width: 12px; height: 12px; fill: var(--accent-red); flex: none; }

  .back-logo {
    position: absolute; left: 34px; bottom: 36px;
    display: flex; align-items: center; gap: 14px;
  }
  .back-logo__square { width: 62px; height: 62px; background: var(--accent-red); }
  .back-logo__name { color: var(--ink-dark); font-weight: 700; font-size: 30px; }
</style>
</head>
<body>
<main class="canvas">
  <section class="card card--front" aria-label="Card front">
    <div class="front-wordmark">DRV Ventures Inc.</div>
    <div class="brand-badge" role="img" aria-label="TORVAN brand badge"></div>
  </section>

  <section class="card card--back" aria-label="Card back">
    <div class="contact">
      <div class="contact__name">Marisol Depree</div>
      <div class="contact__role">CEO</div>
      <div class="contact__address">
        Ground floor, Lindell Plaza Suite 2734<br>
        George Town, Grand Cayman<br>
        Cayman Islands, KY1-4823
      </div>
      <ul class="contact__list">
        <li class="contact__item">
          <svg class="contact__icon" viewBox="0 0 24 24" aria-hidden="true"><path d="M6.6 10.8a15 15 0 0 0 6.6 6.6l2.2-2.2a1 1 0 0 1 1-.25 11.4 11.4 0 0 0 3.6.57 1 1 0 0 1 1 1V20a1 1 0 0 1-1 1A17 17 0 0 1 3 4a1 1 0 0 1 1-1h3.5a1 1 0 0 1 1 1c0 1.25.2 2.45.57 3.6a1 1 0 0 1-.25 1z"/></svg>
          <span>1 555 4180736</span>
        </li>
        <li class="contact__item">
          <svg class="contact__icon" viewBox="0 0 24 24" aria-hidden="true"><path d="M2 5h20v14H2z M3 6l9 7 9-7" stroke="#fff" stroke-width="1.5"/></svg>
          <span>m.depree@drvventuresinc.example</span>
        </li>
        <li class="contact__item">
          <svg class="contact__icon" viewBox="0 0 24 24" aria-hidden="true"><circle cx="12" cy="12" r="10"/><path d="M2 12h20M12 2c3 3 3 17 0 20M12 2c-3 3-3 17 0 20" stroke="#fff" stroke-width="1.4" fill="none"/></svg>
          <span>www.drvventuresinc.example</span>
        </li>
      </ul>
    </div>
    <div class="back-logo">
      <div class="back-logo__square" aria-hidden="true"></div>
      <div class="back-logo__name">DRV Ventures Inc.</div>
    </div>
  </section>
</main>
</body>
</html>
```